Modern Business Card

Modern professional business card with more than just logo and demographic info. Something memorable.

We are a trendy/modern chiropractic group with an emphasis on neurology, hence the minimalist-type brain logo. We want to convey that modern and technical aspect with professionalism and the elite nature of our practice environment.

```html
<!DOCTYPE html>
<html lang="en">
<head>
<meta charset="utf-8">
<title>Meridian Chiropractic – Business Card</title>
<link rel="stylesheet" href="https://fonts.googleapis.com/css2?family=Crimson+Text:wght@400&family=Lato:wght@400&family=Roboto:wght@400;700&display=swap">
<style>
  :root {
    --page: #f1f2f4;
    --card-white: #ffffff;
    --brand-blue: #4a80c2;
    --brand-blue-light: #5a8fcd;
    --brand-blue-deep: #3f72b2;
    --tint: #e6ebf5;
    --ink: #1c1c1c;
    --on-blue: #ffffff;
    --band-dark: #6b6d70;
    --band-light: #d9dadc;
  }
  * { box-sizing: border-box; margin: 0; padding: 0; }
  html, body { width: 1200px; height: 1200px; overflow: hidden; background: var(--page); }
  .canvas { position: relative; width: 1200px; height: 1200px; }

  .card { position: absolute; overflow: hidden; box-shadow: 0 6px 18px rgba(0,0,0,0.18); }
  .card--front { left: 232px; top: 173px; width: 705px; height: 408px; background: var(--card-white); }
  .card--back { left: 231px; top: 629px; width: 702px; height: 400px; background: var(--brand-blue); }

  .front__texture {
    position: absolute; left: 331px; top: 0; width: 374px; height: 187px;
    background:
      radial-gradient(ellipse 60% 80% at 60% 30%, var(--tint) 0%, rgba(230,235,245,0.55) 55%, rgba(230,235,245,0) 100%),
      linear-gradient(90deg, rgba(230,235,245,0) 0%, rgba(230,235,245,0.7) 45%, var(--tint) 100%);
  }
  .back__texture {
    position: absolute; left: 0; top: 0; width: 380px; height: 400px;
    background:
      radial-gradient(ellipse 55% 45% at 45% 25%, var(--brand-blue-light) 0%, rgba(90,143,205,0) 100%),
      radial-gradient(ellipse 50% 45% at 50% 80%, var(--brand-blue-deep) 0%, rgba(63,114,178,0) 100%);
  }

  .front__band {
    position: absolute; left: 0; top: 187px; width: 100%; height: 13px;
    background: linear-gradient(90deg, var(--band-dark) 0%, var(--band-dark) 25%, var(--band-light) 52%, var(--band-dark) 80%, var(--band-dark) 100%);
  }
  .front__panel { position: absolute; left: 0; top: 200px; width: 100%; height: 208px; background: var(--brand-blue); }

  .wordmark { position: absolute; display: flex; align-items: center; font-family: "Crimson Text", serif; font-weight: 400; }
  .wordmark__mark { flex: none; }
  .wordmark__name { display: flex; flex-direction: column; line-height: 1; text-transform: uppercase; }
  .wordmark--front { left: 50px; top: 50px; color: var(--ink); }
  .wordmark--front .wordmark__mark { width: 52px; height: 52px; background: var(--brand-blue); margin-right: 56px; }
  .wordmark--front .wordmark__primary { font-size: 60px; letter-spacing: 0.5px; }
  .wordmark--front .wordmark__secondary { font-size: 33px; margin-top: -4px; }

  .wordmark--back { left: 110px; top: 140px; color: var(--on-blue); }
  .wordmark--back .wordmark__mark { width: 70px; height: 70px; background: var(--on-blue); margin-right: 64px; }
  .wordmark--back .wordmark__primary { font-size: 76px; letter-spacing: 1px; }
  .wordmark--back .wordmark__secondary { font-size: 44px; margin-top: -6px; }

  .person { position: absolute; left: 50px; top: 250px; color: var(--on-blue); }
  .person__name { font-family: "Roboto", sans-serif; font-weight: 700; font-size: 26px; letter-spacing: 0.3px; }
  .person__title { font-family: "Roboto", sans-serif; font-size: 21px; margin-top: 4px; }
  .person__address { font-family: "Lato", sans-serif; font-size: 19px; line-height: 24px; margin-top: 8px; font-style: normal; }

  .contact { position: absolute; left: 421px; top: 253px; list-style: none; color: var(--on-blue); font-family: "Lato", sans-serif; font-size: 19px; }
  .contact__item { display: flex; align-items: center; height: 27.5px; }
  .contact__icon { width: 20px; height: 20px; margin-right: 9px; fill: none; stroke: var(--on-blue); stroke-width: 1.6; }
</style>
</head>
<body>
<main class="canvas">

  <section class="card card--front" aria-label="Card front">
    <div class="front__texture" role="img" aria-label="Faint decorative brand pattern"></div>

    <div class="wordmark wordmark--front">
      <span class="wordmark__mark" aria-hidden="true"></span>
      <span class="wordmark__name">
        <span class="wordmark__primary">Meridian</span>
        <span class="wordmark__secondary">Chiropractic</span>
      </span>
    </div>

    <div class="front__band"></div>
    <div class="front__panel"></div>

    <div class="person">
      <p class="person__name">MARLOW KEANE</p>
      <p class="person__title">President</p>
      <address class="person__address">48 Harbor Lane Suite 200<br>Westfield, NY 10542</address>
    </div>

    <ul class="contact">
      <li class="contact__item">
        <svg class="contact__icon" viewBox="0 0 20 20" aria-hidden="true"><rect x="5.5" y="1.5" width="9" height="17" rx="1.5"/><line x1="5.5" y1="4.5" x2="14.5" y2="4.5"/><line x1="5.5" y1="15" x2="14.5" y2="15"/></svg>
        014 2275 6830
      </li>
      <li class="contact__item">
        <svg class="contact__icon" viewBox="0 0 20 20" aria-hidden="true"><path d="M2 8c0-3 16-3 16 0l-3 1-1-2H6L5 9z" fill="#fff"/><path d="M5 10h10l2 7H3z"/><circle cx="10" cy="13.5" r="2"/></svg>
        014 2275 6830
      </li>
      <li class="contact__item">
        <svg class="contact__icon" viewBox="0 0 20 20" aria-hidden="true"><rect x="1.5" y="4" width="15" height="11"/><path d="M1.5 4l7.5 6 7.5-6"/><circle cx="15" cy="14.5" r="3.5" fill="#fff" stroke="none"/><path d="M13.3 14.5l1.3 1.3 2.2-2.4" stroke="#4a80c2"/></svg>
        hello@meridianchiro.com
      </li>
      <li class="contact__item">
        <svg class="contact__icon" viewBox="0 0 20 20" aria-hidden="true"><circle cx="10" cy="10" r="8"/><ellipse cx="10" cy="10" rx="3.5" ry="8"/><line x1="2" y1="10" x2="18" y2="10"/><path d="M3.5 5.5h13M3.5 14.5h13"/></svg>
        www.meridianchiro.com
      </li>
    </ul>
  </section>

  <section class="card card--back" aria-label="Card back">
    <div class="back__texture" role="img" aria-label="Soft tonal brand pattern"></div>
    <div class="wordmark wordmark--back">
      <span class="wordmark__mark" aria-hidden="true"></span>
      <span class="wordmark__name">
        <span class="wordmark__primary">Meridian</span>
        <span class="wordmark__secondary">Chiropractic</span>
      </span>
    </div>
  </section>

</main>
</body>
</html>
```